The Copperline Collective's website for high impact furniture promotions

I am looking for a simple website. we are a promotional company that runs events for furniture stores to increase sales for short periods of time. i would like the website to have about 4 areas to explain our company. I would like it to be simple and user friendly. I would like a link to chatterbook and a contact section. I am attaching our logo that i would like somewhere large or possibly in the backround. I am open to different color schemes. I would like to convey fast paced, modern, reliable. I am open to all different styles and look forward to seeing whats out there. we are looking for a quick turn around, so if we see one that we like quick, we will pick that one thanks
Reason: looking for some really creative designs and want to give a fair amount of time to produce
Target Market(s)
Retail Furniture store owners
Industry/Entity Type
It Company
Number of Pages Required
1 page
Colors
Designer to choose colors to be used in the design.
Look and feel

```html
<!DOCTYPE html>
<html lang="en">
<head>
<meta charset="utf-8">
<title>The Copperline Collective — Furniture Promotional Events</title>
<link href="https://fonts.googleapis.com/css2?family=PT+Serif:wght@400;700&display=swap" rel="stylesheet">
<style>
:root{
  --white:#ffffff;
  --ink:#1c1c1c;
  --body-text:#6b6b6b;
  --copper:#a8702f;
  --tan:#b48a5c;
  --band-brown:#7a4f1c;
  --band-brown-dark:#4d300f;
  --grey-bg:#e9e9e9;
  --dark:#262626;
  --dark-2:#3a3a3a;
  --serif:"PT Serif", Georgia, serif;
}
*{box-sizing:border-box;margin:0;padding:0}
html,body{width:1200px;height:4813px;overflow:hidden}
body{font-family:var(--serif);color:var(--ink);background:var(--white);position:relative}
a{color:inherit;text-decoration:none}

/* Header */
.site-header{position:absolute;top:0;left:0;width:1200px;height:96px;background:var(--white);z-index:3}
.main-nav{position:absolute;top:38px;font-size:14px;letter-spacing:.5px;display:flex;gap:40px}
.main-nav.left{left:190px}
.main-nav.right{right:190px}
.brand-badge{position:absolute;left:490px;top:0;width:220px;height:150px;z-index:4}
.brand-badge svg{position:absolute;inset:0}
.brand-badge .brand-mark{position:absolute;left:88px;top:14px;width:44px;height:44px;border-radius:50%;background:var(--copper)}
.brand-badge .brand-name{position:absolute;left:0;top:64px;width:220px;text-align:center;font-size:12px;line-height:14px;letter-spacing:1.5px;color:var(--copper);font-weight:700}

/* Hero */
.hero{position:absolute;top:96px;left:0;width:1200px;height:466px;overflow:hidden}
.hero-photo{position:absolute;inset:0;background:linear-gradient(180deg,#6f6b66 0%,#4e4a45 40%,#2e2a26 75%,#3b3630 100%)}
.hero-content{position:absolute;top:175px;left:0;width:1200px;text-align:center;color:var(--white)}
.hero-title{font-size:50px;font-weight:400;letter-spacing:1px;line-height:60px}
.hero-sub{font-size:16px;letter-spacing:1px;margin-top:4px}
.hero-actions{margin-top:26px;display:flex;justify-content:center;gap:28px}
.btn{display:inline-block;font-size:10px;letter-spacing:1px;text-transform:uppercase;border-radius:20px;text-align:center}
.btn-tan{background:var(--tan);color:var(--white)}
.btn-outline{border:2px solid var(--white);color:var(--white)}
.btn-dark{background:#111;color:var(--white)}
.hero-actions .btn{width:150px;height:34px;line-height:32px}
.slider-dots{position:absolute;top:404px;left:0;width:1200px;display:flex;justify-content:center;gap:16px}
.slider-dots span{width:8px;height:8px;border-radius:50%;background:var(--white);opacity:.7}
.slider-dots span:first-child{background:var(--tan);opacity:1}

/* Welcome */
.welcome{position:absolute;top:562px;left:0;width:1200px;height:472px;color:var(--white);text-align:center}
.welcome-photo{position:absolute;inset:0;background:linear-gradient(180deg,var(--band-brown) 0%,#6a4316 55%,var(--band-brown-dark) 100%)}
.welcome-inner{position:relative;padding-top:108px}
.eyebrow{font-size:16px;letter-spacing:1.5px;text-transform:uppercase}
.section-title{font-size:50px;font-weight:400;line-height:60px}
.welcome-text{width:830px;margin:38px auto 0;font-size:13px;line-height:22px;opacity:.92}
.welcome .btn{margin-top:46px;width:150px;height:36px;line-height:36px}

/* Four areas */
.areas{position:absolute;top:1034px;left:0;width:1200px;height:1688px;background:var(--white)}
.areas-head{position:absolute;top:108px;width:1200px;text-align:center}
.areas-head .eyebrow{color:var(--ink);font-size:15px}
.areas-head .section-title{color:var(--ink);margin-top:12px}
.area-row{position:absolute;left:176px;width:850px;height:280px}
.area-photo{position:absolute;top:0;width:414px;height:280px}
.area-row.image-left .area-photo{left:0}
.area-row.image-left .area-copy{left:440px}
.area-row.image-right .area-photo{left:434px;width:416px}
.area-row.image-right .area-copy{left:0}
.area-copy{position:absolute;top:36px;width:390px}
.area-title{font-size:19px;font-weight:400;letter-spacing:.5px;text-transform:uppercase}
.area-text{margin-top:22px;font-size:12px;line-height:19px;color:var(--body-text)}
.area-copy .btn{margin-top:22px;width:146px;height:34px;line-height:34px}

/* Promotional events */
.events{position:absolute;top:2722px;left:0;width:1200px;height:1136px;background:var(--grey-bg)}
.events-head{position:absolute;top:80px;width:1200px;text-align:center}
.events-head .eyebrow{font-size:15px}
.events-head .section-title{color:var(--copper);margin-top:8px}
.event-card{position:absolute;width:416px;height:407px;overflow:hidden}
.event-photo{position:absolute;inset:0}
.event-label{position:absolute;left:16px;top:136px;width:214px;padding:12px 16px 16px;background:rgba(40,40,40,.55);color:var(--white)}
.event-label h3{font-size:36px;font-weight:400;line-height:34px}
.event-label .btn-view{display:inline-block;margin-top:14px;border:1px solid var(--white);font-size:13px;padding:6px 14px}

/* Contact */
.contact{position:absolute;top:3858px;left:0;width:1200px;height:755px;color:var(--white)}
.contact-photo{position:absolute;inset:0;background:linear-gradient(180deg,#4a4a4a 0%,#2b2b2b 45%,#1e1e1e 100%)}
.contact-head{position:absolute;top:96px;width:1200px;text-align:center}
.contact-head .eyebrow{font-size:15px}
.contact-head .section-title{color:var(--copper);margin-top:8px}
.field{position:absolute;height:58px;border:1px solid rgba(255,255,255,.25);background:rgba(20,20,20,.45);font-size:12px;padding:18px 20px;color:#cfcfcf}
.field.message{height:135px}
.contact .btn-submit{position:absolute;left:525px;top:574px;width:150px;height:38px;line-height:38px}
.social-link{position:absolute;top:662px;left:0;width:1200px;display:flex;justify-content:center;align-items:center;gap:8px;font-size:12px}
.social-link .dot{width:18px;height:18px;border-radius:50%;border:1px solid var(--white)}

/* Footer */
.site-footer{position:absolute;top:4613px;left:0;width:1200px;height:200px;background:var(--white);text-align:center}
.footer-brand{position:absolute;top:26px;left:0;width:1200px}
.footer-brand .brand-mark{width:46px;height:46px;border-radius:50%;background:var(--copper);margin:0 auto}
.footer-brand .brand-name{margin-top:8px;font-size:12px;line-height:14px;letter-spacing:1.5px;color:var(--copper);font-weight:700}
.copyright{position:absolute;top:150px;left:0;width:1200px;font-size:14px;color:var(--ink)}
</style>
</head>
<body>

<header class="site-header">
  <nav class="main-nav left"><a href="#">HOME</a><a href="#">ABOUT US</a><a href="#">SERVICES</a></nav>
  <nav class="main-nav right"><a href="#">EVENTS</a><a href="#">FAQ'S</a><a href="#">CONTACT US</a></nav>
</header>
<div class="brand-badge">
  <svg width="220" height="150" viewBox="0 0 220 150"><path d="M0 0 H220 V96 L110 150 L0 96 Z" fill="#ffffff"/></svg>
  <div class="brand-mark"></div>
  <div class="brand-name">THE COPPERLINE<br>COLLECTIVE</div>
</div>

<section class="hero">
  <div class="hero-photo" role="img" aria-label="Outdoor terrace with modern lounge sofas overlooking hills at dusk"></div>
  <div class="hero-content">
    <h1 class="hero-title">COPPERLINE COLLECTIVE</h1>
    <p class="hero-sub">FURNITURE PROMOTIONAL EVENTS</p>
    <div class="hero-actions"><a class="btn btn-tan" href="#">Register Now</a><a class="btn btn-outline" href="#">Learn More</a></div>
  </div>
  <div class="slider-dots"><span></span><span></span><span></span><span></span></div>
</section>

<section class="welcome">
  <div class="welcome-photo" role="img" aria-label="Warm brown toned furniture showroom interior"></div>
  <div class="welcome-inner">
    <p class="eyebrow">Welcome to</p>
    <h2 class="section-title">COPPERLINE COLLECTIVE</h2>
    <p class="welcome-text">Our team plans and runs short, high energy sales events for furniture retailers. We bring the staff, the signage and the buzz, so your floor fills with eager buyers and your stock moves fast. Every event is planned around your store, your goals and your calendar, with clear reporting once the doors close.</p>
    <a class="btn btn-dark" href="#">Register Now</a>
  </div>
</section>

<section class="areas">
  <div class="areas-head">
    <p class="eyebrow">Our four areas</p>
    <h2 class="section-title">COPPERLINE COLLECTIVE</h2>
  </div>

  <article class="area-row image-left" style="top:292px">
    <div class="area-photo" role="img" aria-label="Two shoppers relaxing on a sofa in a furniture store" style="background:linear-gradient(135deg,#b7a48c,#8c7a64 60%,#6e5f4d)"></div>
    <div class="area-copy">
      <h3 class="area-title">Major Furniture Retailer</h3>
      <p class="area-text">We partner with major furniture retailers to stage focused sales weekends. Our crews know the showroom floor, the product and the buyer, and we turn short windows of time into strong, measurable results for every store.</p>
      <a class="btn btn-tan" href="#">Read More</a>
    </div>
  </article>

  <article class="area-row image-right" style="top:626px">
    <div class="area-photo" role="img" aria-label="Woman resting in a cosy armchair with a drink" style="background:linear-gradient(135deg,#e8e2d8,#c9b9a2 55%,#8f7556)"></div>
    <div class="area-copy">
      <h3 class="area-title">Powerful Advertising</h3>
      <p class="area-text">Our advertising reaches local shoppers through print, radio and online channels at once. Each campaign is timed to the event so that the store is busy from the first hour of opening until the final sale.</p>
      <a class="btn btn-tan" href="#">Read More</a>
    </div>
  </article>

  <article class="area-row image-left" style="top:972px">
    <div class="area-photo" role="img" aria-label="Furniture showroom floor filled with patterned sofas" style="background:linear-gradient(180deg,#6a6560,#8e857b 50%,#4b4640)"></div>
    <div class="area-copy">
      <h3 class="area-title">Furniture Sales</h3>
      <p class="area-text">Trained sales staff join your team on the floor for the length of the event. They greet every guest, guide each purchase and help close deals quickly, while your own people stay free to serve loyal clients.</p>
      <a class="btn btn-tan" href="#">Read More</a>
    </div>
  </article>

  <article class="area-row image-right" style="top:1313px">
    <div class="area-photo" role="img" aria-label="Merchandiser arranging red and grey sofas in a showroom" style="background:linear-gradient(180deg,#5c5a58 0%,#9a2a25 35%,#6b6a6a 70%,#3e3d3c)"></div>
    <div class="area-copy">
      <h3 class="area-title">Power Merchandising</h3>
      <p class="area-text">We rework displays, pricing tags and room settings so that every piece looks its best. Smart merchandising draws shoppers deeper into the store and lifts the value of each sale during the promotion.</p>
      <a class="btn btn-tan" href="#">Read More</a>
    </div>
  </article>
</section>

<section class="events">
  <div class="events-head">
    <p class="eyebrow">Furniture</p>
    <h2 class="section-title">PROMOTIONAL EVENTS</h2>
  </div>

  <article class="event-card" style="left:176px;top:209px">
    <div class="event-photo" role="img" aria-label="Grey room with a black chair and pendant lights" style="background:linear-gradient(90deg,#8a6a4a 0%,#b9b6b1 30%,#d6d3ce 100%)"></div>
    <div class="event-label"><h3>Furniture New Trend Models</h3><a class="btn-view" href="#">View Details</a></div>
  </article>
  <article class="event-card" style="left:610px;top:209px">
    <div class="event-photo" role="img" aria-label="Wooden garden table and chairs on a lawn" style="background:linear-gradient(180deg,#121212 0%,#2a2a22 40%,#5a6e2a 75%,#3d4a1e)"></div>
    <div class="event-label"><h3>Urban New Trend Models</h3><a class="btn-view" href="#">View Details</a></div>
  </article>
  <article class="event-card" style="left:176px;top:636px">
    <div class="event-photo" role="img" aria-label="Green armchair beside a wooden side table under a white lamp" style="background:linear-gradient(180deg,#dcdcdc 0%,#c8c8c6 60%,#a7a39d)"></div>
    <div class="event-label"><h3>Classic New Trend Models</h3><a class="btn-view" href="#">View Details</a></div>
  </article>
  <article class="event-card" style="left:610px;top:636px">
    <div class="event-photo" role="img" aria-label="Wooden chairs and a potted plant on a terracotta patio" style="background:linear-gradient(180deg,#1a1a1a 0%,#3b4a2a 35%,#a8683a 70%,#c7854a)"></div>
    <div class="event-label"><h3>Creative New Trend Models</h3><a class="btn-view" href="#">View Details</a></div>
  </article>
</section>

<section class="contact">
  <div class="contact-photo" role="img" aria-label="Dimly lit lounge with sofas"></div>
  <div class="contact-head">
    <p class="eyebrow">Get in touch</p>
    <h2 class="section-title">CONTACT US</h2>
  </div>
  <div class="field" style="left:250px;top:225px;width:344px">Name</div>
  <div class="field" style="left:610px;top:225px;width:343px">E-Mail</div>
  <div class="field" style="left:250px;top:308px;width:344px">Phone</div>
  <div class="field" style="left:610px;top:308px;width:343px">Location</div>
  <div class="field message" style="left:250px;top:392px;width:703px">Message</div>
  <a class="btn btn-tan btn-submit" href="#">Submit</a>
  <a class="social-link" href="#"><span class="dot"></span>chatterbook</a>
</section>

<footer class="site-footer">
  <div class="footer-brand">
    <div class="brand-mark"></div>
    <div class="brand-name">THE COPPERLINE<br>COLLECTIVE</div>
  </div>
  <p class="copyright">© 2017 Company Name | All Rights Reserved</p>
</footer>

</body>
</html>
```